Concierge Healthcare Business Card Design and Logo

We need a logo and business card design for a new company called "Sound Haven". We will provide concierge audiological care, hearing aids, hearing exams, custom hearing protection etc to patients in the comfort of their homes and offices. We would like a sleek and modern design preferably with an Ear related logo.

Target Market(s)

People with hearing loss, Hunters, Musicians
My usual clientele are older individuals so usually 50+ years old

Industry/Entity Type

Health Care

Contact Information for Business Card

Celia Brandt, AuD
Audiologist
512-648-2917
soundhaven@mailvoro.com
www.soundhaven-vorel.com

Logo Text

Sound Haven

Number of Pages Required

3 page

```html
<!DOCTYPE html>
<html lang="en">
<head>
<meta charset="utf-8">
<title>Sound Haven – Business Card</title>
<link rel="stylesheet" href="https://fonts.googleapis.com/css2?family=Cinzel:wght@400;600&display=swap">
<style>
  :root {
    --page-bg: #e6e6e4;
    --card-black: #221f20;
    --brand-blue: #2aa6df;
    --text-light: #f2f2f2;
    --band-blue: #c9e3ea;
    --band-ink: #2a2728;
  }
  * { box-sizing: border-box; margin: 0; padding: 0; }
  html, body { width: 1200px; height: 900px; overflow: hidden; }
  body {
    background: var(--page-bg);
    font-family: "Cinzel", serif;
    position: relative;
  }
  .card {
    position: absolute;
    left: 260px;
    width: 680px;
    height: 389px;
    background: var(--card-black);
    overflow: hidden;
    box-shadow: 0 6px 18px rgba(0,0,0,0.18);
  }
  .card--front { top: 40px; }
  .card--contact { top: 471px; }

  .brand {
    display: flex;
    align-items: center;
    gap: 14px;
    color: var(--brand-blue);
    font-weight: 400;
    letter-spacing: 1px;
  }
  .brand__dot {
    border-radius: 50%;
    background: var(--brand-blue);
    flex: none;
  }
  .card--front .brand {
    position: absolute;
    left: 0; right: 0; top: 0; bottom: 0;
    justify-content: center;
    font-size: 44px;
  }
  .card--front .brand__dot { width: 30px; height: 30px; }

  .card--contact .brand {
    position: absolute;
    left: 70px;
    top: 78px;
    font-size: 28px;
  }
  .card--contact .brand__dot { width: 20px; height: 20px; }

  .person {
    position: absolute;
    right: 48px;
    top: 185px;
    text-align: right;
  }
  .person__name {
    color: var(--brand-blue);
    font-size: 27px;
    letter-spacing: 1px;
    line-height: 1.1;
  }
  .person__title {
    color: var(--text-light);
    font-size: 18px;
    letter-spacing: 1px;
    margin-top: 2px;
  }
  .divider {
    position: absolute;
    left: 48px;
    right: 36px;
    top: 262px;
    height: 1px;
    background: var(--brand-blue);
  }
  .contacts {
    position: absolute;
    right: 36px;
    top: 285px;
    display: flex;
    gap: 18px;
    color: var(--text-light);
    font-size: 17px;
    letter-spacing: 0.5px;
  }
  .contacts__item { display: flex; align-items: center; gap: 8px; }
  .icon { flex: none; }
  .web-band {
    position: absolute;
    left: 0; right: 0; bottom: 0;
    height: 58px;
    background: var(--band-blue);
    display: flex;
    align-items: center;
    padding: 0 36px 0 0;
  }
  .web-band__rule {
    flex: 1;
    height: 1px;
    background: var(--band-ink);
    margin-right: 16px;
  }
  .web-band__url {
    display: flex;
    align-items: center;
    gap: 10px;
    color: var(--band-ink);
    font-size: 20px;
    letter-spacing: 0.5px;
  }
</style>
</head>
<body>
  <section class="card card--front">
    <div class="brand">
      <span class="brand__dot"></span>
      <span class="brand__name">Sound Haven</span>
    </div>
  </section>

  <section class="card card--contact">
    <div class="brand">
      <span class="brand__dot"></span>
      <span class="brand__name">Sound Haven</span>
    </div>

    <div class="person">
      <p class="person__name">Celia Brandt, AuD</p>
      <p class="person__title">Audiologist</p>
    </div>

    <div class="divider"></div>

    <div class="contacts">
      <span class="contacts__item">
        <svg class="icon" width="20" height="14" viewBox="0 0 20 14" aria-hidden="true">
          <rect x="1" y="1" width="18" height="12" fill="none" stroke="#2aa6df" stroke-width="1.5"/>
          <polyline points="1,1 10,8 19,1" fill="none" stroke="#2aa6df" stroke-width="1.5"/>
        </svg>
        SOUNDHAVEN@MAILVORO.COM
      </span>
      <span class="contacts__item">
        <svg class="icon" width="20" height="20" viewBox="0 0 20 20" aria-hidden="true">
          <circle cx="10" cy="10" r="9" fill="none" stroke="#2aa6df" stroke-width="1.5"/>
          <path d="M6.5 5.5 l2 0 l1 2.5 l-1.3 1 q1 2 2.8 2.8 l1-1.3 l2.5 1 l0 2 q-1 1 -2.5 .8 q-5-1.5-6.3-6.3 q-.2-1.5 .8-2.5z" fill="#2aa6df"/>
        </svg>
        512-648-2917
      </span>
    </div>

    <div class="web-band">
      <span class="web-band__rule"></span>
      <span class="web-band__url">
        <svg class="icon" width="20" height="20" viewBox="0 0 20 20" aria-hidden="true">
          <circle cx="10" cy="10" r="9" fill="none" stroke="#2a2728" stroke-width="1.5"/>
          <ellipse cx="10" cy="10" rx="4" ry="9" fill="none" stroke="#2a2728" stroke-width="1.2"/>
          <line x1="1" y1="10" x2="19" y2="10" stroke="#2a2728" stroke-width="1.2"/>
        </svg>
        WWW.SOUNDHAVEN-VOREL.COM
      </span>
    </div>
  </section>
</body>
</html>
```